Business cards in digital learning for freelancer

Hello, I need a business cards in french. I work in the Digital learning industries as freeelancer; I'm an expert in digital learning. I work in France. My customer are in the health industry, pharmaceutical industry, and training organization. I've got a logo. I offer three services: consulting, Design, and Training. In the consulting, I offers coaching to choose your digital learning tools and the digital learning strategy. For the Design, I product differents level of elearning like rapid-learning, elearning, micro-learning, video-learning. And for the training service, I've create training about pedagogy, digital learning management project, Digital learning design.
I join my Logo create in this platform. My universe is gamified. I like the life, and I'm very social. I want a card like I'm I. I love Art (painting), Europeen comics. I use in my visual support "permanent maker" font and caracters. I would like cards: elegant, modern, Top class. If you need any information, you can ask me.
thanks for ideas

Target Market(s)

in health industries and training organization for Training manager, instructor, human resources director

Contact Information for Business Card

Phone number : 06 71 38 95 14 , mail: bastiengolmier@quelmoto.fr, web: bastiengolmier.fr , Carrivo

Font styles to use
Sans Serif

Requirements
Must have
• Use my logo and write my 3 services (consulting, training, design)

```html
<!DOCTYPE html>
<html lang="fr">
<head>
<meta charset="utf-8">
<title>Golmier Digital Learning – Cartes de visite</title>
<link rel="stylesheet" href="https://fonts.googleapis.com/css2?family=Roboto:wght@400;500;900&display=swap">
<style>
  :root {
    --bg: #1f1f1f;
    --orange: #f07325;
    --grey: #707070;
    --ink: #333333;
    --white: #ffffff;
  }
  * { box-sizing: border-box; margin: 0; padding: 0; }
  html, body {
    width: 1200px; height: 988px; overflow: hidden;
    background: var(--bg);
    font-family: "Roboto", Arial, sans-serif;
  }
  .stage { position: relative; width: 1200px; height: 988px; }

  .card {
    position: absolute;
    width: 580px; height: 330px;
    border-radius: 22px;
    overflow: hidden;
  }

  /* Front */
  .card--front {
    left: 90px; top: 100px;
    background: var(--orange);
    color: var(--white);
    display: flex; flex-direction: column; align-items: center; justify-content: center;
  }
  .brand {
    display: flex; align-items: center; gap: 12px;
  }
  .brand__mark {
    width: 22px; height: 22px; border-radius: 50%;
    background: currentColor;
  }
  .brand__name {
    font-weight: 900; font-size: 44px; letter-spacing: 2px;
  }
  .brand__sub {
    font-weight: 500; font-size: 13px; letter-spacing: 3px;
    margin-top: 6px;
  }
  .services {
    list-style: none; display: flex; gap: 30px;
    margin-top: 36px; font-size: 19px; letter-spacing: 2px;
  }
  .services li::before {
    content: ""; display: inline-block;
    width: 7px; height: 7px; border-radius: 50%;
    background: var(--white); margin-right: 7px; vertical-align: middle;
  }

  /* Back */
  .card--back {
    left: 530px; top: 560px;
    background: var(--white);
    color: var(--ink);
  }
  .card--back .brand {
    position: absolute; left: 36px; top: 38px;
    color: var(--orange);
  }
  .card--back .brand__name { font-size: 30px; }
  .card--back .brand__mark { width: 16px; height: 16px; }
  .card--back .brand__sub {
    position: absolute; left: 36px; top: 80px;
    color: var(--grey); font-size: 10px;
  }
  .artwork {
    position: absolute; right: 0; top: 0;
    width: 270px; height: 330px;
    background: radial-gradient(circle at 40% 45%, #7a7a7a 0%, #6c6c6c 45%, rgba(240,115,37,.85) 75%, var(--white) 100%);
  }
  .person {
    position: absolute; left: 36px; top: 150px;
    padding-left: 14px;
    border-left: 5px solid var(--orange);
  }
  .person__name {
    color: var(--orange); font-weight: 900; font-size: 24px; letter-spacing: .5px;
  }
  .person__role { font-size: 15px; margin-top: 2px; }
  .contact {
    position: absolute; left: 55px; top: 220px;
    list-style: none; font-size: 14px; line-height: 23px;
  }
  .contact li { display: flex; align-items: center; gap: 8px; }
  .contact svg { width: 12px; height: 12px; fill: var(--orange); flex: none; }
</style>
</head>
<body>
<main class="stage">

  <section class="card card--front" aria-label="Recto">
    <div class="brand">
      <span class="brand__mark"></span>
      <span class="brand__name">GOLMIER</span>
    </div>
    <div class="brand__sub">DIGITAL LEARNING</div>
    <ul class="services">
      <li>Consulting</li>
      <li>Training</li>
      <li>Design</li>
    </ul>
  </section>

  <section class="card card--back" aria-label="Verso">
    <div class="brand">
      <span class="brand__mark"></span>
      <span class="brand__name">GOLMIER</span>
    </div>
    <div class="brand__sub">DIGITAL LEARNING</div>

    <div class="artwork" role="img" aria-label="Grande illustration d'un cerveau gris traversé par un arbre orange aux branches en spirale"></div>

    <div class="person">
      <p class="person__name">BASTIEN GOLMIER</p>
      <p class="person__role">Creative Director</p>
    </div>

    <ul class="contact">
      <li>
        <svg viewBox="0 0 24 24" aria-hidden="true"><path d="M6.6 10.8a15.1 15.1 0 0 0 6.6 6.6l2.2-2.2c.3-.3.7-.4 1-.2 1.1.4 2.3.6 3.6.6.6 0 1 .4 1 1V20c0 .6-.4 1-1 1A17 17 0 0 1 3 4c0-.6.4-1 1-1h3.5c.6 0 1 .4 1 1 0 1.3.2 2.5.6 3.6.1.3 0 .7-.2 1z"/></svg>
        06 71 38 95 14
      </li>
      <li>
        <svg viewBox="0 0 24 24" aria-hidden="true"><path d="M2 5h20v14H2z M2 5l10 8 10-8" /></svg>
        bastiengolmier@quelmoto.fr
      </li>
      <li>
        <svg viewBox="0 0 24 24" aria-hidden="true"><circle cx="12" cy="12" r="10"/></svg>
        www.bastiengolmier.fr
      </li>
      <li>
        <svg viewBox="0 0 24 24" aria-hidden="true"><circle cx="12" cy="12" r="10"/></svg>
        Carrivo @bastiengolmier
      </li>
    </ul>
  </section>

</main>
</body>
</html>
```